Dietitian needs awesome business card

I need a contemporary design that's eye catching but professional.
My card is to given to doctors, specialists and patients alike.
I manage patients with chronic diseases
I have uploaded my logo and current business card, I would also like the other Certified Clinical Nutritionist logo incorporated into the design

Target Market(s)

Doctors, specialists and patients

Industry/Entity Type

Healthcare

Contact Information for Business Card

www.brightfieldnutrition.com.au
Ph: 0427 561 903
Fax: 6457 2183
email: marcus.k.diet@fernmail.com
Space on the back of the card with: Appointment date, Appointment time and appointment location

Font styles to use
Serif

Colors
fbee3e
876aae
ffc214

Requirements
Must have
• My Logo
• Certified Clinical Nutritionist Logo
• My 4 locations - Pinebrook Medical Centre, North Corrin Health, Hollis Medical, Ashcombe Doctors Surgery
Nice to have
• I like the colours in my current business card

```html
<!DOCTYPE html>
<html lang="en">
<head>
<meta charset="utf-8">
<title>Brightfield Nutrition – Business Card</title>
<link href="https://fonts.googleapis.com/css2?family=Lora:ital,wght@0,400;0,600;0,700;1,400&display=swap" rel="stylesheet">
<style>
  :root {
    --backdrop: #262626;
    --card-white: #ffffff;
    --card-mint: #ecf5de;
    --navy: #1f3c8f;
    --green: #8cc63f;
    --purple: #876aae;
    --gold: #ffc214;
    --yellow: #fbee3e;
    --text-grey: #444444;
    --band-dark: #1e2a78;
    --band-light: #0a7fd1;
    --line-grey: #9aa3c0;
  }
  * { margin: 0; padding: 0; box-sizing: border-box; }
  html, body {
    width: 1200px; height: 987px; overflow: hidden;
    background: var(--backdrop);
    font-family: "Lora", Georgia, serif;
  }
  .card {
    position: absolute; left: 293px; width: 615px; height: 352px; overflow: hidden;
  }
  .card--front { top: 130px; background: var(--card-white); }
  .card--back { top: 505px; background: var(--card-mint); }

  .brand { position: absolute; display: flex; align-items: center; }
  .brand__dot { border-radius: 50%; background: var(--green); flex: none; }
  .brand__name { color: var(--navy); font-weight: 400; line-height: 1.05; }

  .card--front .brand { left: 318px; top: 34px; gap: 14px; }
  .card--front .brand__dot { width: 78px; height: 78px; }
  .card--front .brand__name { font-size: 31px; }

  .holder__name {
    position: absolute; left: 26px; top: 160px;
    font-size: 22px; font-weight: 700; color: var(--navy);
  }
  .holder__role {
    position: absolute; left: 26px; top: 191px;
    font-size: 15px; color: var(--purple);
  }
  .badge {
    position: absolute; left: 507px; top: 176px; width: 74px; height: 34px;
    background: var(--gold);
  }
  .badge__seal {
    position: absolute; right: 6px; top: 4px; width: 26px; height: 26px;
    border-radius: 50%; background: var(--card-white);
  }
  .divider {
    position: absolute; left: 26px; top: 219px; width: 555px; height: 1px;
    background: var(--yellow);
  }
  .contacts { position: absolute; left: 26px; top: 232px; list-style: none; }
  .contacts li {
    display: flex; align-items: center; gap: 8px;
    height: 23.5px; font-size: 14.5px; color: var(--text-grey);
  }
  .contacts svg { width: 16px; height: 16px; fill: var(--navy); flex: none; }

  .accent-line {
    position: absolute; left: 0; top: 321px; width: 100%; height: 3px;
    background: var(--gold);
  }
  .accent-band {
    position: absolute; left: 0; top: 327px; width: 100%; height: 25px;
    background: linear-gradient(90deg, var(--band-dark), var(--band-light) 45%, var(--band-dark));
  }

  .card--back .brand {
    left: 0; right: 0; top: 26px; flex-direction: column; gap: 10px;
  }
  .card--back .brand__dot { width: 72px; height: 72px; }
  .card--back .brand__name { font-size: 19px; }
  .website {
    position: absolute; left: 0; right: 0; top: 152px; text-align: center;
    font-size: 16px; font-style: italic; color: var(--navy);
  }
  .locations {
    position: absolute; left: 0; right: 0; top: 186px; list-style: none;
    display: flex; justify-content: center; gap: 8px;
    font-size: 12px; color: var(--purple);
  }
  .locations li + li::before {
    content: "•"; color: var(--gold); margin-right: 8px;
  }
  .appointment { position: absolute; left: 41px; color: var(--navy); font-size: 16px; }
  .appointment__field { position: absolute; display: flex; align-items: flex-end; white-space: nowrap; }
  .appointment__blank {
    display: inline-block; height: 1px; background: var(--line-grey);
    margin: 0 6px 5px 8px;
  }
  .appointment__unit { font-size: 12px; }
</style>
</head>
<body>

<section class="card card--front" aria-label="Business card front">
  <div class="brand">
    <span class="brand__dot"></span>
    <span class="brand__name">Brightfield<br>Nutrition</span>
  </div>

  <h1 class="holder__name">Marcus Kendrick</h1>
  <p class="holder__role">Nutritionist &amp; Chef</p>
  <div class="badge" aria-label="Certified Clinical Nutritionist badge"><span class="badge__seal"></span></div>
  <div class="divider"></div>

  <ul class="contacts">
    <li>
      <svg viewBox="0 0 24 24" aria-hidden="true"><path d="M6.6 10.8a15.1 15.1 0 0 0 6.6 6.6l2.2-2.2a1 1 0 0 1 1-.25 11.4 11.4 0 0 0 3.6.57 1 1 0 0 1 1 1V20a1 1 0 0 1-1 1A17 17 0 0 1 3 4a1 1 0 0 1 1-1h3.5a1 1 0 0 1 1 1c0 1.25.2 2.45.57 3.6a1 1 0 0 1-.25 1z"/></svg>
      0427 561 903
    </li>
    <li>
      <svg viewBox="0 0 24 24" aria-hidden="true"><path d="M6 2h12v6H6zM3 9h18a1 1 0 0 1 1 1v7h-4v5H6v-5H2v-7a1 1 0 0 1 1-1zm5 8v3h8v-3z"/></svg>
      6457 2183
    </li>
    <li>
      <svg viewBox="0 0 24 24" aria-hidden="true"><path d="M2 5h20v14H2zm2 2v.5l8 5 8-5V7zm0 2.9V17h16V9.9l-8 5z"/></svg>
      marcus.k.diet@fernmail.com
    </li>
  </ul>

  <div class="accent-line"></div>
  <div class="accent-band"></div>
</section>

<section class="card card--back" aria-label="Business card back">
  <div class="brand">
    <span class="brand__dot"></span>
    <span class="brand__name">Brightfield Nutrition</span>
  </div>
  <p class="website">www.brightfieldnutrition.com.au</p>
  <ul class="locations" aria-label="Clinic locations">
    <li>Pinebrook Medical Centre</li>
    <li>North Corrin Health</li>
    <li>Hollis Medical</li>
    <li>Ashcombe Doctors Surgery</li>
  </ul>

  <div class="appointment" style="top:242px">
    <div class="appointment__field" style="left:0">Date :<span class="appointment__blank" style="width:250px"></span></div>
    <div class="appointment__field" style="left:313px">Time :<span class="appointment__blank" style="width:112px"></span><span class="appointment__unit">AM/PM</span></div>
  </div>
  <div class="appointment" style="top:292px">
    <div class="appointment__field" style="left:0">Location :<span class="appointment__blank" style="width:440px"></span></div>
  </div>
</section>

</body>
</html>
```